Brightline Energy Product Distribution Brochure

We are looking to have our current brochure for our customers completely redesigned...the idea is to present the relevant information in an attractive way . Our website is brightlineenergyco.example where you can find more information about us. We have included a file with a rough idea of the page order and what each should include but feel free to adapt based on design. The example provided is only for context and doesnt have to be maintained. We will be using the brochure both digitally and in print form. As long as it reads easily and is eye catching, the design can be horizontal or vertical.Final deliverable should be indesign file.

"Our Brands" page: should be limited to one page (space being enough) where it has the header for each one (for example diesel generators) space for one or two lines of text and then the corresponding logos for each of the five categories
Updates

For those asking: the "our brands" page should be a single page layout where there is a header with the corresponding section and space for maybe one line of text followed by the two logos for that category. Each of the product pages should be similar in fashion to the one in the document attached: a photo of the product with some white space and space for the text to be included. We will be posting additional examples today

Target Market(s)

We want to present it to customers both digitally and in print so they can see our products

Industry/Entity Type

Power Generation

Font styles to use
Serif

Requirements
Must have
• Eye catching and able to present the information in a presentable fashion. Rest is up to you.
Nice to have
• Should incorporate the colors of our logo but can also add other depending on design

```html
<!DOCTYPE html>
<html lang="en">
<head>
<meta charset="utf-8">
<title>Brightline Energy – Brochure Inside Pages</title>
<link href="https://fonts.googleapis.com/css2?family=Montserrat:ital,wght@0,300;0,400;0,700;1,300&display=swap" rel="stylesheet">
<style>
  :root {
    --yellow: #fcca05;
    --ink: #1e1e1e;
    --muted: #5a5a5a;
    --paper: #ffffff;
    --stage: #ffffff;
    --placeholder-dark: #2a2a2a;
    --placeholder-light: #e9e9ec;
  }
  * { box-sizing: border-box; margin: 0; padding: 0; }
  html, body { width: 1200px; height: 1200px; overflow: hidden; background: var(--stage); }
  body { position: relative; font-family: "Montserrat", sans-serif; color: var(--ink); }

  .spread-label {
    position: absolute; top: 134px;
    font-family: "Montserrat", sans-serif; font-weight: 300; font-style: italic;
    font-size: 24px; color: var(--muted); letter-spacing: 0.5px;
  }
  .spread-label--left { left: 37px; }
  .spread-label--right { left: 613px; }

  .page {
    position: absolute; width: 554px; height: 784px; background: var(--paper);
    overflow: hidden; box-shadow: 0 30px 50px rgba(0,0,0,0.18), 0 4px 10px rgba(0,0,0,0.06);
  }
  .page--nine { left: 30px; top: 208px; }
  .page--ten { left: 611px; top: 209px; }

  .page__art { position: absolute; inset: 0; width: 100%; height: 100%; }

  .section-tag { position: absolute; top: 35px; left: 0; display: flex; align-items: center; }
  .section-tag__bar { width: 47px; height: 10px; background: var(--yellow); }
  .section-tag__text { margin-left: 9px; font-size: 11.5px; font-weight: 400; letter-spacing: 0.2px; }

  .brand { position: absolute; top: 40px; right: 50px; display: flex; align-items: center; gap: 6px; }
  .brand__mark { width: 11px; height: 11px; background: var(--yellow); }
  .brand__name { font-size: 9px; font-weight: 400; letter-spacing: 0.6px; color: var(--ink); text-transform: uppercase; }

  .page__title {
    position: absolute; top: 96px; left: 48px;
    font-size: 35px; font-weight: 300; letter-spacing: -0.5px; white-space: nowrap;
  }
  .page__subtitle {
    position: absolute; top: 157px; left: 48px;
    font-size: 16px; font-weight: 700; color: var(--yellow); letter-spacing: 0.2px;
  }
  .page__body {
    position: absolute; top: 184px; left: 48px; width: 192px;
    font-size: 9.2px; line-height: 11.2px; text-align: justify; hyphens: auto;
  }

  .product-photo { position: absolute; border-radius: 4px; }
  .product-photo--alternator {
    left: 282px; top: 432px; width: 240px; height: 188px;
    background: radial-gradient(ellipse at 55% 45%, #4a4a4a 0%, var(--placeholder-dark) 55%, #111 100%);
  }
  .product-photo--regulator {
    left: 300px; top: 431px; width: 200px; height: 208px;
    background: linear-gradient(170deg, #3a3a3a 0%, var(--placeholder-dark) 70%, var(--placeholder-light) 100%);
  }

  .page__footer { position: absolute; top: 938px; }
  .folio { position: absolute; bottom: 29px; left: 48px; font-size: 7px; font-weight: 700; }
  .web { position: absolute; bottom: 29px; left: 100px; font-size: 7px; font-weight: 700; letter-spacing: 0.1px; text-transform: uppercase; }
</style>
</head>
<body>

<p class="spread-label spread-label--left">Inside</p>
<p class="spread-label spread-label--right">Inside</p>

<!-- Page 9 -->
<section class="page page--nine">
  <svg class="page__art" viewBox="0 0 693 980" preserveAspectRatio="none" aria-hidden="true">
    <defs>
      <linearGradient id="shade9" x1="0" y1="0" x2="1" y2="1">
        <stop offset="0" stop-color="#000" stop-opacity="0.06"/>
        <stop offset="1" stop-color="#000" stop-opacity="0"/>
      </linearGradient>
    </defs>
    <polygon points="511,368 693,550 693,745 440,500" fill="url(#shade9)"/>
    <polygon points="0,675 106,675 460,318 511,368 213,665 493,943 693,745 693,855 568,980 0,980" fill="var(--yellow)"/>
    <polygon points="106,675 0,675 0,980 400,980" fill="#000" opacity="0.04"/>
    <polyline points="693,85 518,260 693,435" fill="none" stroke="var(--yellow)" stroke-width="1.5"/>
    <polyline points="0,395 140,535 0,675" fill="none" stroke="var(--yellow)" stroke-width="1.5"/>
  </svg>

  <div class="section-tag"><span class="section-tag__bar"></span><span class="section-tag__text">OUR STOCK</span></div>
  <div class="brand"><span class="brand__mark"></span><span class="brand__name">Brightline Energy</span></div>

  <h1 class="page__title">AC ALTERNATORS</h1>
  <h2 class="page__subtitle">CONTROLLERS</h2>
  <p class="page__body">Fugiant pelluptatis rempe nectibea nati nobitate voluptatur, verum dolorerrum velectur, ut fugit aut aborporepe volluptatem in pro beatios molendi genihillis non nonsequ aersped estius seque volupis es sanis ad que volupta quamus ipic te videndene solum esercid que re audam, nonem es atempos re nim cus et volorument fuga. Da am fugia ipidel maios everum ut venient officit quidi ut quo</p>

  <div class="product-photo product-photo--alternator" role="img" aria-label="Product photo of a black industrial AC alternator"></div>

  <span class="folio">9</span>
  <span class="web">brightlineenergyco.example</span>
</section>

<!-- Page 10 -->
<section class="page page--ten">
  <svg class="page__art" viewBox="0 0 693 980" preserveAspectRatio="none" aria-hidden="true">
    <defs>
      <linearGradient id="shade10" x1="0" y1="0" x2="1" y2="1">
        <stop offset="0" stop-color="#000" stop-opacity="0.06"/>
        <stop offset="1" stop-color="#000" stop-opacity="0"/>
      </linearGradient>
    </defs>
    <polygon points="511,368 693,550 693,745 440,500" fill="url(#shade10)"/>
    <polygon points="0,675 106,675 460,318 511,368 213,665 493,943 693,745 693,855 568,980 0,980" fill="var(--yellow)"/>
    <polygon points="106,675 0,675 0,980 400,980" fill="#000" opacity="0.04"/>
    <polyline points="693,85 518,260 693,435" fill="none" stroke="var(--yellow)" stroke-width="1.5"/>
    <polyline points="0,395 140,535 0,675" fill="none" stroke="var(--yellow)" stroke-width="1.5"/>
  </svg>

  <div class="section-tag"><span class="section-tag__bar"></span><span class="section-tag__text">OUR STOCK</span></div>
  <div class="brand"><span class="brand__mark"></span><span class="brand__name">Brightline Energy</span></div>

  <h1 class="page__title">ALTERNATOR PARTS</h1>
  <h2 class="page__subtitle">CONTROLLERS</h2>
  <p class="page__body">Fugiant pelluptatis rempe nectibea nati nobitate voluptatur, verum dolorerrum velectur, ut fugit aut aborporepe volluptatem in pro beatios molendi genihillis non nonsequ aersped estius seque volupis es sanis ad que volupta quamus ipic te videndene solum esercid que re audam, nonem es atempos re nim cus et volorument fuga. Da am fugia ipidel maios everum ut venient officit quidi ut quo</p>

  <div class="product-photo product-photo--regulator" role="img" aria-label="Product photo of a voltage regulator circuit board on a clear stand"></div>

  <span class="folio">10</span>
  <span class="web">brightlineenergyco.example</span>
</section>

</body>
</html>
```